Coastline Premier Retreats Business Card Design

Design a business card for Coastline Premier Retreats. Look at the website for colors and reference. Card should have logo, name, title, office number, mobile number, email, URL and a tagline like, "Luxury Hotel & Resort Email Marketing" (This might change).

https://www.coastlinepremierretreats.example

The rest I will leave up to your imagination.

Contact Information for Business Card

Logo, name, title, office number, mobile number, email, URL and a tagline like, "Luxury Hotel & Resort Email Marketing" (This might change).

```html
<!DOCTYPE html>
<html lang="en">
<head>
<meta charset="UTF-8">
<title>Coastline Premier Retreats – Business Card</title>
<link rel="stylesheet" href="https://fonts.googleapis.com/css2?family=Montserrat:wght@600;700&family=Open+Sans:wght@400;600&display=swap">
<style>
  :root {
    --stage: #232323;
    --orange: #f47621;
    --orange-deep: #d9601a;
    --ink: #1f2024;
    --ink-mid: #26272c;
    --ink-soft: #2c2d33;
    --white: #ffffff;
    --grey: #d9d9de;
  }
  * { box-sizing: border-box; margin: 0; padding: 0; }
  html, body { width: 1200px; height: 780px; overflow: hidden; background: var(--stage); }
  .canvas { position: relative; width: 1200px; height: 780px; }

  .card {
    position: absolute; top: 110px; width: 330px; height: 560px;
    border-radius: 26px; overflow: hidden;
    box-shadow: 0 18px 40px rgba(0,0,0,.55);
  }

  /* back */
  .card-back { left: 235px; background: var(--orange); }
  .back-mark {
    position: absolute; left: 50%; top: 50%;
    transform: translate(-50%, -50%) rotate(-90deg);
    white-space: nowrap; display: flex; align-items: center; gap: 14px;
  }
  .back-mark .mark-square { width: 22px; height: 22px; background: var(--orange-deep); }
  .back-mark .mark-name {
    font-family: "Montserrat", sans-serif; font-weight: 700;
    font-size: 28px; letter-spacing: 1px; color: var(--orange-deep); text-transform: uppercase;
  }

  /* front */
  .card-front { left: 635px; background: var(--ink); }
  .front-waves { position: absolute; inset: 0; }
  .front-content { position: relative; height: 100%; text-align: center; color: var(--white); }

  .brand {
    position: absolute; top: 48px; left: 0; right: 0;
    display: flex; justify-content: center; align-items: center; gap: 10px;
  }
  .brand .mark-square { width: 12px; height: 12px; background: var(--orange); }
  .brand .brand-name {
    font-family: "Montserrat", sans-serif; font-weight: 700; font-size: 16px;
    letter-spacing: .5px; color: var(--white); text-transform: uppercase;
  }

  .person { position: absolute; top: 182px; left: 0; right: 0; }
  .person-name { font-family: "Montserrat", sans-serif; font-weight: 700; font-size: 27px; line-height: 1.1; }
  .person-name .first { color: var(--orange); }
  .person-title { font-family: "Open Sans", sans-serif; font-size: 14px; color: var(--grey); margin-top: 4px; }

  .icons { display: flex; justify-content: center; gap: 10px; margin-top: 16px; }
  .icon { width: 24px; height: 24px; border-radius: 50%; background: var(--orange); display: flex; align-items: center; justify-content: center; }
  .icon svg { width: 13px; height: 13px; }

  .contacts { list-style: none; margin-top: 14px; font-family: "Open Sans", sans-serif; font-size: 12.5px; line-height: 1.55; color: var(--white); }

  .tagline {
    position: absolute; bottom: 46px; left: 0; right: 0;
    font-family: "Open Sans", sans-serif; font-weight: 600; font-size: 14px; line-height: 1.45; color: var(--orange);
  }
</style>
</head>
<body>
<main class="canvas">

  <section class="card card-back" aria-label="Card back">
    <div class="back-mark">
      <span class="mark-square"></span>
      <span class="mark-name">Coastline Premier Retreats</span>
    </div>
  </section>

  <section class="card card-front" aria-label="Card front">
    <svg class="front-waves" viewBox="0 0 330 560" preserveAspectRatio="none" aria-hidden="true">
      <rect width="330" height="560" fill="var(--ink-mid)"/>
      <path d="M0 0 H330 V420 Q250 520 90 500 L0 500 Z" fill="var(--ink-soft)" opacity=".6"/>
      <path d="M0 0 H330 V330 Q290 440 120 445 L0 445 Z" fill="var(--ink)"/>
    </svg>
    <div class="front-content">
      <div class="brand">
        <span class="mark-square"></span>
        <span class="brand-name">Coastline Premier Retreats</span>
      </div>

      <div class="person">
        <h1 class="person-name"><span class="first">Marina</span> Velasquez</h1>
        <p class="person-title">Co-Founder</p>

        <div class="icons">
          <span class="icon" aria-label="Office phone">
            <svg viewBox="0 0 16 16"><path d="M3 2l3 1 1 3-2 1a8 8 0 004 4l1-2 3 1 1 3c-1 1-2 1-3 1C6 14 2 10 2 5c0-1 0-2 1-3z" fill="#fff"/></svg>
          </span>
          <span class="icon" aria-label="Mobile phone">
            <svg viewBox="0 0 16 16"><rect x="4.5" y="1.5" width="7" height="13" rx="1.5" fill="none" stroke="#fff" stroke-width="1.6"/><circle cx="8" cy="12" r=".9" fill="#fff"/></svg>
          </span>
          <span class="icon" aria-label="Email">
            <svg viewBox="0 0 16 16"><rect x="1.5" y="3.5" width="13" height="9" rx="1" fill="none" stroke="#fff" stroke-width="1.5"/><path d="M2 4l6 5 6-5" fill="none" stroke="#fff" stroke-width="1.5"/></svg>
          </span>
          <span class="icon" aria-label="Website">
            <svg viewBox="0 0 16 16"><circle cx="8" cy="8" r="6" fill="none" stroke="#fff" stroke-width="1.5"/><path d="M2 8h12M8 2c-3 3-3 9 0 12M8 2c3 3 3 9 0 12" fill="none" stroke="#fff" stroke-width="1.2"/></svg>
          </span>
        </div>

        <ul class="contacts">
          <li>(555) 014-2758</li>
          <li>(555) 019-7777</li>
          <li>www.coastlinepremierretreats.example</li>
          <li>info@coastlinepremierretreats.example</li>
        </ul>
      </div>

      <p class="tagline">Luxury Hotel &amp;<br>Resort Email Marketing</p>
    </div>
  </section>

</main>
</body>
</html>
```